Mindfulness School for Children -- Business Cards

We're looking for business cards for our school directors and owners. We're a mindfulness school for children called little lanterns. Attached are our logos/icons.

```html
<!DOCTYPE html>
<html lang="en">
<head>
<meta charset="utf-8">
<title>little lanterns — business cards</title>
<link rel="stylesheet" href="https://fonts.googleapis.com/css2?family=Alegreya:wght@500&family=Lato:wght@400&family=Montserrat:wght@800&display=swap">
<style>
  :root {
    --backdrop: #1c1c1c;
    --kraft-light: #dfbf93;
    --kraft-mid: #c49a68;
    --kraft-dark: #a5774a;
    --ink: #161210;
  }
  * { margin: 0; padding: 0; box-sizing: border-box; }
  html, body {
    width: 1093px;
    height: 1200px;
    overflow: hidden;
    background: var(--backdrop);
  }
  .canvas {
    position: relative;
    width: 1093px;
    height: 1200px;
  }
  .card {
    position: absolute;
    left: 264px;
    width: 580px;
    height: 357px;
    background: linear-gradient(140deg, var(--kraft-light) 0%, var(--kraft-mid) 55%, var(--kraft-dark) 100%);
    color: var(--ink);
    text-align: center;
  }
  .card--front { top: 226px; }
  .card--back { top: 620px; }

  .person-name {
    position: absolute;
    top: 70px;
    width: 100%;
    font-family: "Montserrat", sans-serif;
    font-weight: 800;
    font-size: 20px;
    letter-spacing: 0.2px;
  }
  .person-role {
    position: absolute;
    top: 92px;
    width: 100%;
    font-family: "Lato", sans-serif;
    font-size: 16px;
  }
  .rule {
    position: absolute;
    left: 243px;
    width: 94px;
    height: 1px;
    background: var(--ink);
  }
  .rule--top { top: 124px; }
  .rule--bottom { top: 223px; }
  .contact-list,
  .address {
    position: absolute;
    width: 100%;
    list-style: none;
    font-family: "Lato", sans-serif;
    font-size: 16.5px;
    line-height: 21px;
  }
  .contact-list { top: 141px; }
  .address { top: 241px; font-style: normal; }

  .brand-name {
    position: absolute;
    top: 158px;
    width: 100%;
    font-family: "Alegreya", serif;
    font-weight: 500;
    font-size: 50px;
    line-height: 56px;
    letter-spacing: -0.5px;
  }
</style>
</head>
<body>
<main class="canvas">
  <section class="card card--front" aria-label="Card front">
    <h1 class="person-name">DANIEL HART</h1>
    <p class="person-role">Managing Director</p>
    <div class="rule rule--top"></div>
    <ul class="contact-list">
      <li>M: 044-987 654 321</li>
      <li>E: hello@littlelanterns.com</li>
      <li>W: www.littlelanterns.com</li>
    </ul>
    <div class="rule rule--bottom"></div>
    <address class="address">
      48, Willow Lane Road<br>
      Brookfield, 560041.
    </address>
  </section>

  <section class="card card--back" aria-label="Card back">
    <p class="brand-name">little lanterns</p>
  </section>
</main>
</body>
</html>
```